Brightfield Learning Enrichment Academy

We need a signage design for our Brightfield Learning Academic Enrichment Academy. We provide tutoring and enrichment to students grades 1-8 in math, science and reading, and also give life skills. We also provide quarterly community services initiatives and athletic skills clinics.
We want to be the place that parents can take their kids that need tutoring, enrichment, or sharpen their skills for the next academic school year. Our program has been in existence since 2012, and we are moving into our first facility. We want something that stands out from the busy street that our building is located on.
Please visit www.brightfieldlearners.org for more information on our organization.
Using the letters acronym B.L.E in a favorable fashion would be fantastic if at all possible
Thanks.

Target Market(s)

Parents with students in grades 1st-8th
Students who seek to prepare for grade level enrichment
Grant providers who seek reputable programs that are actually doing the work of mentoring, tutoring students

Industry/Entity Type

Tutoring

Font styles to use
Other font styles liked:
• the collegiate font

Colors
0255a3
85acd3
cee9f5

Requirements
Must have
• B.L.E as some form of acronym
Should not have
• N/A

```html
<!DOCTYPE html>
<html lang="en">
<head>
<meta charset="utf-8">
<title>Brightfield Learning Academy – Signage</title>
<link rel="stylesheet" href="https://fonts.googleapis.com/css2?family=Varela+Round&display=swap">
<style>
  :root {
    --backdrop: #e4e6e8;
    --sign-white: #fbfbfb;
    --blue-deep: #0255a3;
    --blue-main: #1a8ad6;
    --blue-bright: #3aa6e6;
    --blue-soft: #85acd3;
    --blue-pale: #cee9f5;
    --text-white: #ffffff;
    --mark-grey: #7d8c99;
  }
  * { margin: 0; padding: 0; box-sizing: border-box; }
  html, body {
    width: 1200px;
    height: 1000px;
    overflow: hidden;
    background: var(--backdrop);
    font-family: "Varela Round", "Arial Rounded MT Bold", sans-serif;
  }
  .sign {
    position: absolute;
    left: 40px;
    top: 52px;
    width: 1120px;
    height: 896px;
    background: var(--sign-white);
    box-shadow: 0 6px 18px rgba(0, 0, 0, 0.12);
    overflow: hidden;
  }
  .sign__panel {
    position: absolute;
    left: 188px;
    top: 140px;
    width: 932px;
    height: 612px;
    border-radius: 46px 0 0 46px;
    overflow: hidden;
    background:
      radial-gradient(ellipse at 30% 20%, rgba(133, 172, 211, 0.45), transparent 55%),
      linear-gradient(135deg, var(--blue-bright) 0%, var(--blue-main) 50%, var(--blue-deep) 100%);
  }
  .sign__athletes {
    position: absolute;
    left: 14px;
    top: 40px;
    width: 500px;
    height: 572px;
    border-radius: 36px 36px 0 36px;
    background: linear-gradient(160deg, rgba(206, 233, 245, 0.55) 0%, rgba(133, 172, 211, 0.35) 60%, rgba(255, 255, 255, 0.12) 100%);
  }
  .sign__title {
    position: absolute;
    left: 530px;
    top: 92px;
    color: var(--text-white);
    font-weight: 400;
  }
  .sign__acronym {
    display: block;
    font-size: 200px;
    line-height: 1;
    letter-spacing: -4px;
  }
  .sign__name {
    display: block;
    margin-top: 8px;
    font-size: 68px;
    line-height: 84px;
  }
  .sign__mark {
    position: absolute;
    z-index: 2;
    left: 24px;
    top: 782px;
    display: flex;
    align-items: center;
    gap: 10px;
    color: var(--mark-grey);
    font-size: 20px;
    line-height: 1.2;
  }
  .sign__mark-square {
    width: 40px;
    height: 40px;
    background: var(--blue-pale);
  }
</style>
</head>
<body>
  <main class="sign">
    <section class="sign__panel">
      <div class="sign__athletes" role="img" aria-label="White silhouettes of athletes: a soccer player kicking a ball, a basketball player, a baseball batter and a lacrosse player"></div>
      <h1 class="sign__title">
        <span class="sign__acronym">BLE</span>
        <span class="sign__name">Brightfield<br>Learning<br>Academy</span>
      </h1>
    </section>
    <div class="sign__mark">
      <span class="sign__mark-square"></span>
      <span>Brightfield<br>Learning</span>
    </div>
  </main>
</body>
</html>
```